Layout for site fence advertising - length approx. 250 cm x 125 cm

The advertising will later be printed on a PVC film and used for events or on sports fields.

Main services :
Your regional contact at
Real estate and business financing
independent insurance advice

```html
<!DOCTYPE html>
<html lang="en">
<head>
<meta charset="utf-8">
<title>Site Fence Banner – Real Estate and Business Financing</title>
<link rel="stylesheet" href="https://fonts.googleapis.com/css2?family=Bebas+Neue&family=Poppins:wght@400;500;600;700&display=swap">
<style>
  :root {
    --brand-blue: #1a55c4;
    --ink: #1e1e1e;
    --footer-dark: #262626;
    --tab-dark: #3a3a3a;
    --white: #ffffff;
    --page-bg: #e6e6e6;
    --photo-top: #b9c3cf;
    --photo-bottom: #8c8a6e;
  }
  * { box-sizing: border-box; margin: 0; padding: 0; }
  html, body {
    width: 943px; height: 1200px; overflow: hidden;
    background: var(--page-bg);
  }
  .banner {
    position: absolute; left: 41px; top: 385px;
    width: 861px; height: 429px;
    background: var(--white);
    overflow: hidden;
    box-shadow: 0 6px 18px rgba(0,0,0,0.25);
    font-family: "Poppins", sans-serif;
  }
  .banner-shapes { position: absolute; inset: 0; }
  .headline {
    position: absolute; left: 39px; top: 22px;
    font-family: "Bebas Neue", sans-serif; font-weight: 400;
    font-size: 72px; line-height: 57px; letter-spacing: -0.5px;
  }
  .headline .line-blue { color: var(--brand-blue); display: block; }
  .headline .line-dark { color: var(--ink); display: block; }
  .services-tab {
    position: absolute; left: 50px; top: 143px;
    color: var(--white); font-size: 21px; line-height: 30px;
    font-weight: 400; letter-spacing: 0.3px;
  }
  .services-tab strong { font-weight: 600; }
  .service-list {
    position: absolute; left: 42px; top: 181px;
    display: grid; grid-template-columns: 178px 160px; row-gap: 6px;
    list-style: none;
  }
  .service-item {
    display: flex; align-items: center; gap: 9px;
    color: var(--white); font-weight: 600; font-size: 20px; line-height: 28px;
  }
  .service-icon { width: 24px; height: 24px; flex: none; }
  .advisor-name {
    position: absolute; left: 41px; top: 259px;
    font-size: 32px; font-weight: 700; color: var(--ink); line-height: 40px;
    letter-spacing: 0.3px;
  }
  .advisor-role {
    position: absolute; left: 41px; top: 300px;
    font-family: "Bebas Neue", sans-serif;
    font-size: 37px; line-height: 40px; color: var(--ink);
  }
  .advisor-role span { color: var(--brand-blue); }
  .firm-name {
    position: absolute; left: 599px; top: 30px;
    display: flex; align-items: center; gap: 13px;
  }
  .firm-name .dot {
    width: 58px; height: 58px; border-radius: 50%;
    border: 3px solid var(--brand-blue); flex: none;
  }
  .firm-name .label {
    font-size: 10.5px; font-weight: 600; color: var(--brand-blue); line-height: 14px;
    white-space: nowrap;
  }
  .firm-name .label small {
    display: block; font-size: 8px; font-weight: 600; color: var(--brand-blue);
  }
  .contact-bar {
    position: absolute; left: 0; bottom: 0; width: 100%; height: 82px;
    background: var(--footer-dark);
  }
  .contact-tag {
    position: absolute; left: 41px; top: 19px; height: 31px; width: 308px;
    background: var(--brand-blue);
    clip-path: polygon(0 0, 94% 0, 100% 100%, 0 100%);
    color: var(--white); font-size: 16px; line-height: 31px; padding-left: 12px;
    letter-spacing: 0.2px;
  }
  .contact-tag strong { font-weight: 600; }
  .contact-web {
    position: absolute; left: 357px; top: 14px;
    color: var(--white); font-size: 21px; line-height: 36px;
  }
  .contact-divider {
    position: absolute; left: 612px; top: 10px; height: 52px;
    border-left: 1px dashed rgba(255,255,255,0.8);
  }
  .contact-phone {
    position: absolute; left: 625px; top: 14px;
    color: var(--white); font-size: 21px; line-height: 36px; letter-spacing: 0.5px;
  }
</style>
</head>
<body>
  <section class="banner">
    <svg class="banner-shapes" width="861" height="429" viewBox="0 0 861 429">
      <defs>
        <linearGradient id="photoTone" x1="0" y1="0" x2="0" y2="1">
          <stop offset="0" stop-color="var(--photo-top)"/>
          <stop offset="1" stop-color="var(--photo-bottom)"/>
        </linearGradient>
      </defs>
      <polygon points="0,155 430,155 440,143 440,254 0,254" fill="var(--brand-blue)"/>
      <polygon points="570,0 598,0 440,200 425,180 426,155 548,0" fill="var(--brand-blue)"/>
      <polygon points="41,142 226,142 236,172 41,172" fill="var(--tab-dark)"/>
      <polygon points="440,205 520,112 861,112 861,347 440,347"
               fill="url(#photoTone)"
               role="img" aria-label="Photo area: advisor portrait in front of a city panorama"/>
    </svg>

    <h1 class="headline">
      <span class="line-blue">Real Estate and</span>
      <span class="line-dark">Business Financing</span>
    </h1>

    <p class="services-tab">OUR <strong>SERVICES</strong></p>
    <ul class="service-list">
      <li class="service-item">
        <svg class="service-icon" viewBox="0 0 24 24"><circle cx="12" cy="12" r="11" fill="var(--white)"/><circle cx="12" cy="12" r="8.5" fill="none" stroke="var(--brand-blue)" stroke-width="1.2"/><text x="12" y="16" text-anchor="middle" font-size="10" font-family="Poppins, sans-serif" fill="var(--brand-blue)">$</text></svg>
        Investing
      </li>
      <li class="service-item">
        <svg class="service-icon" viewBox="0 0 24 24"><circle cx="12" cy="12" r="11" fill="var(--white)"/><circle cx="12" cy="12" r="8.5" fill="none" stroke="var(--brand-blue)" stroke-width="1.2"/><rect x="8" y="9" width="8" height="7" fill="none" stroke="var(--brand-blue)" stroke-width="1.2"/></svg>
        Leasing
      </li>
      <li class="service-item">
        <svg class="service-icon" viewBox="0 0 24 24"><circle cx="12" cy="12" r="11" fill="var(--white)"/><circle cx="12" cy="12" r="8.5" fill="none" stroke="var(--brand-blue)" stroke-width="1.2"/><path d="M8 16 V10 L12 7 L16 10 V16 Z" fill="none" stroke="var(--brand-blue)" stroke-width="1.2"/></svg>
        Financing
      </li>
      <li class="service-item">
        <svg class="service-icon" viewBox="0 0 24 24"><circle cx="12" cy="12" r="11" fill="var(--white)"/><circle cx="12" cy="12" r="8.5" fill="none" stroke="var(--brand-blue)" stroke-width="1.2"/><path d="M12 7 L16 9 V12 Q16 15 12 17 Q8 15 8 12 V9 Z" fill="none" stroke="var(--brand-blue)" stroke-width="1.2"/></svg>
        Insurance
      </li>
    </ul>

    <h2 class="advisor-name">LUKAS BRENNER</h2>
    <p class="advisor-role">Independent <span>Insurance Advicer</span></p>

    <div class="firm-name">
      <span class="dot"></span>
      <p class="label">Aurelia Finanzberatung GmbH<small>Finanzieren, Versichern, Vorsorgen</small></p>
    </div>

    <footer class="contact-bar">
      <p class="contact-tag">YOUR REGIONAL <strong>CONTACT AT</strong></p>
      <p class="contact-web">www.aurelia-finanz.at</p>
      <span class="contact-divider"></span>
      <p class="contact-phone">+43 664 210 5871</p>
    </footer>
  </section>
</body>
</html>
```